Zelvo Stationary

Design the stationary of Zelvo Promotions Group.

Zelvo is a BTL company, BTL meaning "below the line". In other words Zelvo is a Promotional Marketing company (the company that design the brands promotional activities).

The design should transmit creativity, agility, boldness.

I need:
* Bis Card
* Letter head
* Envelopes, both vertical and horizontal (for legal size), and letter envelope
* Folders
* PPT template (Title page and regular page)
* CD slip (CD envelope)
* ID card (employee card)

And what ever else you want to throw in.
Updates

Guys,

Something I missed from the brief.   The predominat color should be RED.

Also, have fun and play with the exclamation mark (!) of the logo. 

Hi guys, more comments:

Remember that Zelvo is a "creativity" agency, not in the advertising side but on the promotional side, and that should reflect on the stationary.

 I want a bold design.  Bold and yet crisp.

 

Guys, i just uploaded the Logo in AI format.

I Also uploaded the actual Zelvo Bis Card, wich I like.  So I will like to see some designs with that bis card approach.

Guys, I am so sorry, but I notice in your last post that I upladed a wrong design ("13154_promotions_group_zelvo_brief225630.ai").  The problem was that I asked the designer the file in AI format and he send me thw wrong file, and since I dont have Illustrator I could not verify it.

The differences are minor, I just already ask him the correct one (similar to the EPS file).

Sorry                                   

Just post the correct AI file : "Zelvo Logo.ai"

Reason: I'm expecting more designs to choose from and also I wont be available tomorrow to decide.

Reason: Sorry guys, but we are not there yet!

Target Market(s)

Marketing directors, Marketing Managers

Industry/Entity Type

Legal

Requirements
Must have
• Must work with the logo attached.
The predominat color should be RED.
Play and have fun with the exclamation mark (!).
Should not have
• * No old fonts

Should not be:
* boring
* Informal
* rigid

```html
<!DOCTYPE html>
<html lang="en">
<head>
<meta charset="utf-8">
<title>Zelvo Promotions Group — Stationery</title>
<link href="https://fonts.googleapis.com/css2?family=Barlow:wght@400;500;700;800&family=Barlow+Condensed:wght@400;500&display=swap" rel="stylesheet">
<style>
  :root{
    --red:#d4232b;
    --red-deep:#8e1117;
    --red-dark:#5e0a0e;
    --ink:#1d1d1f;
    --grey:#6b6b6b;
    --band:#e3e3e3;
    --paper:#ffffff;
    --stage:#2e2e30;
  }
  *{box-sizing:border-box;margin:0;padding:0}
  html,body{width:1200px;height:588px;overflow:hidden;background:var(--stage)}
  body{position:relative;font-family:"Barlow",Arial,sans-serif;color:var(--ink)}

  .piece{position:absolute;background:var(--paper);overflow:hidden;box-shadow:0 4px 14px rgba(0,0,0,.35)}

  /* wordmark */
  .brand{display:flex;align-items:center;gap:6px}
  .brand-mark{width:10px;height:10px;background:var(--red);flex:none}
  .brand-name{font-family:"Barlow",Arial,sans-serif;font-weight:800;color:var(--ink);line-height:.9}
  .brand-name .word{display:block;text-transform:lowercase;letter-spacing:-.5px}
  .brand-name .sub{display:block;text-transform:uppercase;letter-spacing:1.6px;font-size:.32em;margin-top:2px}
  .brand.on-dark .brand-name{color:#fff}
  .brand.on-dark .brand-mark{background:#fff}

  /* contact band */
  .contact-band{position:absolute;left:0;right:0;background:var(--band);color:var(--grey);font-family:"Barlow Condensed",Arial,sans-serif;font-size:8px;line-height:1.35;padding:5px 12px}
  .contact-band .icon{color:var(--red)}
  .accent-bar{position:absolute;right:0;top:0;bottom:0;width:46px;background:linear-gradient(180deg,var(--red),var(--red-deep))}
  .accent-bar.short{top:auto;height:45%}

  /* letterhead */
  .letterhead{left:24px;top:70px;width:300px;height:440px}
  .letterhead .brand{position:absolute;left:22px;top:24px;font-size:30px}
  .letter-body{position:absolute;left:22px;top:94px;right:70px;font-size:6.6px;line-height:1.55;color:#333}
  .letter-body p{margin-bottom:6px}
  .letter-body ul{list-style:none;margin:0 0 6px 6px}
  .letter-body li::before{content:"+ ";}
  .signature{width:78px;height:22px;background:linear-gradient(90deg,#e9e9e9,#f5f5f5);margin:4px 0 3px}
  .letterhead .contact-band{bottom:18px;right:46px}

  /* large envelope */
  .envelope-large{left:348px;top:40px;width:420px;height:230px}
  .envelope-large .brand{position:absolute;left:28px;top:24px;font-size:34px}
  .envelope-large .contact-band{bottom:26px;right:46px;font-size:9px}

  /* DL envelope with flap */
  .envelope-dl{left:348px;top:300px;width:420px;height:220px}
  .envelope-dl .flap{position:absolute;left:0;right:0;top:0;height:48px;background:linear-gradient(180deg,var(--red-dark),var(--red));border-radius:0 0 50% 50%/0 0 100% 100%}
  .envelope-dl .brand{position:absolute;left:28px;top:70px;font-size:30px}
  .envelope-dl .contact-band{bottom:22px;right:46px;font-size:9px}

  /* business cards */
  .card{width:186px;height:106px;top:40px;border-radius:5px}
  .card-front{left:792px}
  .card-front .brand{position:absolute;left:14px;top:16px;font-size:20px}
  .card-name{position:absolute;right:0;top:52px;width:92px;background:var(--red);color:#fff;font-size:7.5px;font-weight:700;padding:4px 8px}
  .card-name span{font-weight:400;margin-left:6px}
  .card-contact{position:absolute;left:14px;bottom:10px;font-family:"Barlow Condensed",Arial,sans-serif;font-size:6.5px;color:var(--grey);line-height:1.4}
  .card-contact .icon{color:var(--red)}
  .card-back{left:990px;background:linear-gradient(160deg,var(--red),var(--red-dark));display:flex;align-items:center;justify-content:center}
  .card-back .brand{font-size:22px}

  /* CD sleeve + disc */
  .cd-sleeve{left:792px;top:172px;width:186px;height:186px;background:linear-gradient(180deg,var(--red),var(--red-deep))}
  .cd-sleeve .tab{position:absolute;left:50%;top:-14px;width:40px;height:28px;margin-left:-20px;border-radius:50%;background:var(--red-dark)}
  .cd-sleeve .stripe{position:absolute;left:0;right:0;bottom:28px;height:46px;background:var(--ink)}
  .cd-sleeve .tagline{position:absolute;left:14px;bottom:80px;color:#fff;font-size:8px;letter-spacing:1px;text-transform:uppercase}
  .cd-sleeve .brand{position:absolute;left:14px;bottom:40px;font-size:20px}
  .cd-disc{position:absolute;left:990px;top:172px;width:186px;height:186px;border-radius:50%;background:linear-gradient(180deg,#fafafa 0 44%,var(--ink) 44% 58%,#fafafa 58%);box-shadow:0 4px 14px rgba(0,0,0,.35);overflow:hidden}
  .cd-disc::after{content:"";position:absolute;left:50%;top:50%;width:36px;height:36px;margin:-18px 0 0 -18px;border-radius:50%;background:var(--stage);box-shadow:0 0 0 8px #cfcfcf}
  .cd-disc .accent{position:absolute;right:0;top:0;width:50px;height:100%;background:var(--red)}
  .cd-disc .note{position:absolute;left:56px;top:128px;width:74px;font-size:5px;line-height:1.35;color:var(--grey)}

  /* folder */
  .folder{left:792px;top:384px;width:384px;height:136px;background:linear-gradient(135deg,var(--red),var(--red-dark))}
  .folder .pocket{position:absolute;left:0;right:0;bottom:0;height:52px;background:rgba(0,0,0,.22);border-top:1px solid rgba(255,255,255,.15)}
  .folder .brand{position:absolute;left:22px;top:24px;font-size:28px}
</style>
</head>
<body>

<section class="piece letterhead">
  <div class="brand"><span class="brand-name"><span class="word">Zelvo</span><span class="sub">Promotions Group</span></span><span class="brand-mark"></span></div>
  <div class="letter-body">
    <p>Dear Mr. First Last</p>
    <p>An henismod et wismod magnim euguero consecte dolenim deliquis aliquat, odo od eu faccum il ullandre ing eugiamet, quis at nibh nonsectem do consequat ipsum iuscillaore dolore venim odolorem ad duis nostrud auguera estrud ea aut tie consequisci bla feu nibh ercillaor se tionse.</p>
    <p>Qualifications:</p>
    <ul><li>asdf asdf sadf</li><li>asdf asd fasdf asd</li><li>asdf asdf asdf asd</li></ul>
    <p>Raestie corperat adiam ing eugait dolore dolobor commodolum vel dolor andrero dolum etum quis dolor susnrud ercip eros patinit augait landreet orem duis nonum amco.</p>
    <p>Sincerely,</p>
    <div class="signature" role="img" aria-label="Handwritten signature"></div>
    <p>Martin Oakes</p>
  </div>
  <div class="contact-band">P.O. Box 48210 Harbor City, 30270 Westland<br><span class="icon">&#9742;</span> +000 (4) 555 0181 &nbsp;<span class="icon">&#9742;</span> +000 (4) 555 0182 &nbsp;<span class="icon">@</span> www.zelvopromo.com</div>
  <div class="accent-bar short"></div>
</section>

<section class="piece envelope-large">
  <div class="brand"><span class="brand-name"><span class="word">Zelvo</span><span class="sub">Promotions Group</span></span><span class="brand-mark"></span></div>
  <div class="contact-band">P.O. Box 48210 Harbor City, 30270 Westland &nbsp;<span class="icon">&#9742;</span> +000 (4) 555 0182 &nbsp;<span class="icon">@</span> www.zelvopromo.com</div>
  <div class="accent-bar"></div>
</section>

<section class="piece envelope-dl">
  <div class="flap"></div>
  <div class="brand"><span class="brand-name"><span class="word">Zelvo</span><span class="sub">Promotions Group</span></span><span class="brand-mark"></span></div>
  <div class="contact-band">P.O. Box 48210 Harbor City, 30270 Westland<br><span class="icon">&#9742;</span> +000 (4) 555 0181 &nbsp;<span class="icon">&#9742;</span> +000 (4) 555 0182 &nbsp;<span class="icon">@</span> www.zelvopromo.com</div>
  <div class="accent-bar short"></div>
</section>

<section class="piece card card-front">
  <div class="brand"><span class="brand-name"><span class="word">Zelvo</span><span class="sub">Promotions Group</span></span><span class="brand-mark"></span></div>
  <div class="card-name">Lena Carver<span>CEO</span></div>
  <div class="card-contact">P.O. Box 48210 Harbor City, 30270 Westland<br><span class="icon">&#9742;</span> +000 (4) 555 0181 &nbsp;<span class="icon">@</span> lena@zelvopromo.com<br><span class="icon">@</span> www.zelvopromo.com</div>
</section>

<section class="piece card card-back">
  <div class="brand on-dark"><span class="brand-name"><span class="word">Zelvo</span><span class="sub">Promotions Group</span></span><span class="brand-mark"></span></div>
</section>

<section class="piece cd-sleeve">
  <div class="tab"></div>
  <div class="tagline">Your tagline goes here</div>
  <div class="stripe"></div>
  <div class="brand on-dark"><span class="brand-name"><span class="word">Zelvo</span><span class="sub">Promotions Group</span></span><span class="brand-mark"></span></div>
</section>

<section class="cd-disc">
  <div class="accent"></div>
  <p class="note">Short note about the disc contents and campaign material goes here.</p>
</section>

<section class="piece folder">
  <div class="brand on-dark"><span class="brand-name"><span class="word">Zelvo</span><span class="sub">Promotions Group</span></span><span class="brand-mark"></span></div>
  <div class="pocket"></div>
</section>

</body>
</html>
```